Executive Business Card for Healthcare Company [Need Today]

I need a business card design for a healthcare company. The only branding the company has thus far is a logo. The cards will be utilized by company executives. The design I envision will be vibrant and appealing but with a corporate feel. They shouldn't be too casual or playful. I would like to complete this project TODAY if possible.

Target Market(s)

Healthcare vendors, other executives in healthcare and pharmaceuticals

Industry/Entity Type

Pharmaceutical

Contact Information for Business Card

See attachment

Font styles to use
Serif
Sans Serif

Colors

Designer to choose colors to be used in the design.

```html
<!DOCTYPE html>
<html lang="en">
<head>
<meta charset="utf-8">
<title>Corvale Therapeutics – Business Card</title>
<link href="https://fonts.googleapis.com/css2?family=Hind:wght@300;400;600&display=swap" rel="stylesheet">
<style>
  :root {
    --page: #ffffff;
    --brand-mint: #5cffc5;
    --card-back: #f8fafa;
    --accent: #55e6c3;
    --ring-green: #7cf07c;
    --ink: #6a7177;
    --rule: #9aa0a4;
    --white: #ffffff;
  }
  * { margin: 0; padding: 0; box-sizing: border-box; }
  html, body {
    width: 1200px; height: 1000px; overflow: hidden;
    background: var(--page);
    font-family: "Hind", Arial, sans-serif;
  }
  .canvas { position: relative; width: 1200px; height: 1000px; }

  .card { position: absolute; width: 565px; height: 323px; }
  .card--front { left: 105px; top: 162px; background: var(--brand-mint); }
  .card--back { left: 505px; top: 534px; background: var(--card-back); }

  /* front lockup */
  .front-ring {
    position: absolute; left: 142px; top: 117px;
    width: 88px; height: 88px; border-radius: 50%;
    border: 3px solid var(--white);
  }
  .front-divider {
    position: absolute; left: 240px; top: 143px;
    width: 1px; height: 46px; background: var(--white);
  }
  .front-name {
    position: absolute; left: 252px; top: 128px;
    color: var(--white); font-weight: 300; line-height: 1;
  }
  .front-name .word-main { display: block; font-size: 44px; letter-spacing: 1px; }
  .front-name .word-sub { display: block; font-size: 20px; margin-top: 2px; padding-left: 60px; }

  /* back */
  .back-ring {
    position: absolute; left: 69px; top: 114px;
    width: 96px; height: 96px; border-radius: 50%;
    border: 4px solid var(--ring-green);
    display: flex; align-items: center; justify-content: center;
    color: var(--ring-green); font-weight: 400; font-size: 17px;
  }
  .back-divider {
    position: absolute; left: 234px; top: 53px;
    width: 1px; height: 219px; background: var(--rule);
  }
  .contact { position: absolute; left: 258px; top: 46px; color: var(--ink); }
  .person-name { font-size: 19px; color: var(--accent); letter-spacing: 0.5px; line-height: 1.2; }
  .person-name .first { font-weight: 600; }
  .person-name .last { font-weight: 300; }
  .person-title { font-size: 16.5px; font-weight: 300; margin-top: 1px; letter-spacing: 0.3px; }

  .detail { position: absolute; left: 0; width: 260px; font-size: 16.5px; font-weight: 300; line-height: 23px; letter-spacing: 0.6px; }
  .detail p { padding-left: 32px; }
  .detail svg { position: absolute; left: 2px; }
  .detail--phone { top: 63px; }
  .detail--email { top: 122px; }
  .detail--address { top: 163px; }
</style>
</head>
<body>
<div class="canvas">

  <section class="card card--front">
    <div class="front-ring"></div>
    <div class="front-divider"></div>
    <div class="front-name">
      <span class="word-main">corvale</span>
      <span class="word-sub">therapeutics</span>
    </div>
  </section>

  <section class="card card--back">
    <div class="back-ring">Corvale</div>
    <div class="back-divider"></div>

    <div class="contact">
      <h1 class="person-name"><span class="first">MARTIN</span> <span class="last">HALE</span></h1>
      <h2 class="person-title">Senior Director of Marketing</h2>

      <div class="detail detail--phone">
        <svg width="18" height="18" viewBox="0 0 24 24" style="top:4px">
          <path d="M6.6 10.8a15 15 0 0 0 6.6 6.6l2.2-2.2c.3-.3.7-.4 1-.2 1.1.4 2.3.6 3.6.6.6 0 1 .4 1 1V20c0 .6-.4 1-1 1A17 17 0 0 1 3 4c0-.6.4-1 1-1h3.5c.6 0 1 .4 1 1 0 1.3.2 2.5.6 3.6.1.3 0 .7-.2 1z" fill="none" stroke="var(--accent)" stroke-width="2"/>
          <path d="M14 3a7 7 0 0 1 7 7M14 7a3 3 0 0 1 3 3" fill="none" stroke="var(--accent)" stroke-width="2" stroke-linecap="round"/>
        </svg>
        <p>555-210-4837 office<br>555-382-6190 cell</p>
      </div>

      <div class="detail detail--email">
        <svg width="16" height="13" viewBox="0 0 16 13" style="top:6px">
          <rect x="0" y="0" width="16" height="13" rx="1" fill="var(--accent)"/>
          <path d="M1 1.5 8 7l7-5.5" fill="none" stroke="var(--card-back)" stroke-width="1.4"/>
        </svg>
        <p>mhale@corvalerx.com</p>
      </div>

      <div class="detail detail--address">
        <svg width="13" height="17" viewBox="0 0 13 17" style="top:4px">
          <path d="M6.5 0A6.5 6.5 0 0 0 0 6.5C0 11 6.5 17 6.5 17S13 11 13 6.5A6.5 6.5 0 0 0 6.5 0z" fill="var(--accent)"/>
          <circle cx="6.5" cy="6.5" r="2.5" fill="var(--card-back)"/>
        </svg>
        <p>Corvale Therapeutics, LLC<br>118 W Maple Avenue<br>Lindale, GA 30147</p>
      </div>
    </div>
  </section>

</div>
</body>
</html>
```